Purple Heart Veteran Owned Telecommunications Company

I need to develop my current website (brightwirel.com) into something more upbeat and modern. I created the existing one with SiteKindle and it's very basic. I'm open to using any type of website builder and not just SiteKindle. I feel like SiteKindle is pretty basic. I want something customized to me and my company. I plan on doing a Zorbix Ad, Email Marketing, and Mail Marketing campaign and SEO push. I want a website built so they can look up my company. We are a low voltage telecommunications company based out of Chicago. We are a General Contractor and I have technicians all throughout the US and Canada. I mainly appeal to the government and fortune 500 companies across the country. I focus on commercial and federal work with minor work in Residential. I need to appeal to everyone and not just locally. My company name is Brightwirel. I'm a Marine Corps veteran and my I created the company with my son in mind. We are a service disabled veteran owned small business. I'm open to any play on my logo or color scheme. I do like the color blue but I'm open to anything again. I would like a website that has little maintenance needed and something that is modern and sticks out with my competitors. I'm only in business for 2 years but I need to stick out to my competition so I can start building revenue through ads and getting my name out there with limited funds. I did have a logo and name created which I'm attaching. I'm completely open to changing it if someone can come up with something creative. I would like someone that understands SEO and can help feed work to my site. I'm also open to paying more for the right website that gets everything I want. I know I need to add more pages and more professional. Please use my website as a template but also feel free to come up with any new ideas. I would like some feedback or ideas on what else to add to my website or remove so I can appeal to my audience and look more authentic.

Target Market(s)

Commercial Companies locally in Chicago, and Fortune 500 companies and the government

Industry/Entity Type

Telecommunications

Coding

Number of Pages Required

Font styles to use
Sans Serif

Requirements
Must have
• A Modern, fresh look that is customized and original. Something that sticks out to my customers.
Nice to have
• Anything that sticks out and isn't stock. I'm open to anything that is unique and different.
Should not have
• Nothing Generic. I would like something custom tailored to my business

```html
<!DOCTYPE html>
<html lang="en">
<head>
<meta charset="utf-8">
<title>Brightwirel — Low Voltage Telecommunications</title>
<link href="https://fonts.googleapis.com/css2?family=Poppins:wght@300;400;500;600;700;800&display=swap" rel="stylesheet">
<style>
  :root{
    --navy:#0c2a62;
    --panel:#eff1f5;
    --white:#ffffff;
    --ink:#0c2a62;
    --muted:#6f7480;
    --grey-btn:#5a5a5c;
    --heading-grey:#5b5d62;
    --frame:#e3e7ee;
    --line:rgba(255,255,255,.7);
  }
  *{margin:0;padding:0;box-sizing:border-box}
  html,body{width:1200px;height:2853px;overflow:hidden}
  body{position:relative;background:var(--white);font-family:'Poppins',sans-serif;color:var(--ink)}
  .abs{position:absolute}

  /* Hero */
  .hero{position:absolute;left:0;top:0;width:1200px;height:609px;
    background:linear-gradient(100deg,#3a1550 0%,#1d1f4f 22%,#0f2a48 50%,#0e3340 72%,#0c2236 100%)}
  .brand{position:absolute;left:144px;top:30px;display:flex;align-items:center;gap:10px;
    font-weight:600;font-size:19px;letter-spacing:2px;color:var(--white)}
  .brand-dot{width:22px;height:22px;border-radius:50%;background:var(--white)}
  .nav{position:absolute;top:36px;left:615px;width:440px;font-size:13px;font-weight:500;color:var(--white)}
  .nav span{position:absolute;top:0;white-space:nowrap}
  .nav-line{position:absolute;left:615px;top:63px;width:440px;height:3px;background:var(--white)}
  .nav-active{position:absolute;left:615px;top:60px;width:70px;height:9px;border-radius:5px;background:var(--white)}
  .hero-title{position:absolute;left:142px;top:205px;color:var(--white);font-weight:800;font-size:66px;line-height:1}
  .hero-name{position:absolute;left:142px;top:286px;color:var(--white);font-weight:700;font-size:60px;letter-spacing:9px;line-height:1}
  .hero-sub{position:absolute;left:143px;top:366px;color:var(--white);font-size:21px;font-weight:400}
  .btn-solid{position:absolute;background:var(--navy);color:var(--white);font-size:17px;letter-spacing:2px;
    display:flex;align-items:center;justify-content:center;font-weight:400}
  .dots circle{fill:none;stroke:var(--white);stroke-width:2}
  .dots text{fill:var(--white);font-family:'Poppins',sans-serif;font-weight:600;text-anchor:middle}

  /* What we do */
  .intro-title{position:absolute;left:142px;top:690px;font-size:52px;font-weight:600;color:var(--ink)}
  .intro-sub{position:absolute;left:143px;top:755px;font-size:16px;color:var(--muted)}
  .intro-text{position:absolute;left:143px;width:450px;font-size:13px;line-height:21.5px;color:var(--muted);font-weight:300}

  /* Service rows */
  .row{position:absolute;left:0;width:1200px}
  .photo{position:absolute}
  .svc-title{position:absolute;font-size:24px;font-weight:500}
  .svc-list{position:absolute;font-size:15px;line-height:24.3px;font-weight:400}
  .btn-small{position:absolute;width:132px;height:35px;display:flex;align-items:center;justify-content:center;
    font-size:12.5px;font-weight:600;text-transform:uppercase}

  /* Markets */
  .markets-title{position:absolute;left:0;width:1200px;top:2000px;text-align:center;font-size:36px;font-weight:600;color:var(--heading-grey)}
  .card{position:absolute;top:2070px;width:292px;height:415px;background:var(--white);box-shadow:0 2px 10px rgba(0,0,0,.12)}
  .card .pic{width:292px;height:173px}
  .card h3{margin-top:26px;text-align:center;font-size:19px;font-weight:600;color:#3b3c40}
  .card p{margin:12px auto 0;width:230px;text-align:center;font-size:12.5px;line-height:20px;color:#555}
  .card .more{margin:14px auto 0;width:130px;height:38px;background:var(--grey-btn);color:var(--white);
    display:flex;align-items:center;justify-content:center;font-size:15px;font-weight:500}
  .card.featured{background:var(--navy)}
  .card.featured h3,.card.featured p{color:var(--white)}
  .card.featured .more{background:transparent;border:1px solid var(--white)}

  /* Footer */
  .footer{position:absolute;left:0;top:2553px;width:1200px;height:300px;background:var(--navy);color:var(--white)}
  .footer > *{position:absolute;color:var(--white)}
  .foot-brand{left:143px;top:72px;display:flex;align-items:center;gap:10px;font-size:24px;font-weight:600;letter-spacing:1px;line-height:30px}
  .foot-brand i{width:26px;height:26px;border-radius:50%;background:var(--white);display:block}
  .social{top:177px;width:29px;height:29px;border:1.5px solid var(--white);border-radius:50%}
  .foot-h{font-size:15px;font-weight:500;line-height:22px}
  .contact{left:397px;font-size:15px;font-weight:600;letter-spacing:.3px;line-height:27px;white-space:nowrap}
  .icon{left:362px}
  .foot-link{font-size:12.5px;line-height:19px;white-space:nowrap}
  .divider-v{left:726px;top:41px;width:1px;height:196px;background:var(--line)}
  .divider-h{left:143px;top:237px;width:912px;height:1px;background:var(--line)}
  .copy{left:0;width:1200px;top:257px;text-align:center;font-size:13px;line-height:20px}
</style>
</head>
<body>

<!-- Hero -->
<section class="hero" role="img" aria-label="Technician with a laptop in a server room aisle lit in purple and teal"></section>
<div class="brand"><span class="brand-dot"></span>BRIGHTWIREL</div>
<nav class="nav">
  <span style="left:12px">Home</span>
  <span style="left:80px">Low Voltage</span>
  <span style="left:190px">Markets</span>
  <span style="left:272px">Our Team</span>
  <span style="left:367px">Contact Us</span>
</nav>
<div class="nav-line"></div>
<div class="nav-active"></div>
<h1 class="hero-title">Welcome to</h1>
<div class="hero-name">BRIGHTWIREL</div>
<p class="hero-sub">With over 20 years of proven experience</p>
<div class="btn-solid" style="left:146px;top:407px;width:166px;height:44px">READ MORE</div>
<svg class="abs dots" style="left:1100px;top:278px" width="50" height="120" viewBox="0 0 50 120">
  <circle cx="25" cy="23" r="18"/><text x="25" y="29" font-size="17">01</text>
  <circle cx="25" cy="64" r="13"/><text x="25" y="69" font-size="13">02</text>
  <circle cx="25" cy="101" r="13"/><text x="25" y="106" font-size="13">03</text>
</svg>
<svg class="abs" style="left:562px;top:576px" width="76" height="34" viewBox="0 0 76 34"><polygon points="0,34 38,0 76,34" fill="#fff"/></svg>

<!-- What we do -->
<h2 class="intro-title">What we do</h2>
<p class="intro-sub">With over 20 years of proven experience</p>
<p class="intro-text" style="top:785px">Our past projects include both new construction and repairs/restorations. Occupied and fully operational job sites are never a problem. And we can also plan, manage, and design jobs.</p>
<p class="intro-text" style="top:869px">We offer an end-to-end client experience that includes seamless communication, budgeting, staffing, on-site organization, and solid, quality handiwork every time.</p>
<div class="btn-solid" style="left:143px;top:949px;width:166px;height:43px">READ MORE</div>
<svg class="abs" style="left:595px;top:650px" width="465" height="395" viewBox="0 0 465 395">
  <defs>
    <linearGradient id="techTone" x1="0" y1="0" x2="0" y2="1">
      <stop offset="0" stop-color="#4a4d55"/><stop offset=".55" stop-color="#8a7a6a"/><stop offset="1" stop-color="#d9dbe0"/>
    </linearGradient>
    <filter id="soft" x="-10%" y="-10%" width="120%" height="120%"><feDropShadow dx="0" dy="4" stdDeviation="7" flood-opacity=".18"/></filter>
  </defs>
  <polygon points="6,6 459,6 232,388" fill="var(--frame)" filter="url(#soft)"/>
  <polygon role="img" aria-label="Overhead view of a technician working at a computer desk" points="27,18 438,18 232,366" fill="url(#techTone)"/>
  <polygon points="227,362 237,362 232,370" fill="#3a3d44"/>
</svg>

<!-- Cabling row -->
<div class="row" style="top:1087px;height:287px;background:var(--panel)"></div>
<div class="photo" role="img" aria-label="Blue network patch cables plugged into a switch" style="left:0;top:1087px;width:600px;height:287px;background:linear-gradient(110deg,#2f5f74 0%,#5c8c92 35%,#8a8a6a 70%,#3b4c70 100%)"></div>
<svg class="abs" style="left:560px;top:1087px" width="80" height="40" viewBox="0 0 80 40"><polygon points="0,0 80,0 40,35" fill="var(--panel)"/></svg>
<h3 class="svc-title" style="left:650px;top:1130px;color:var(--ink)">Cabling</h3>
<p class="svc-list" style="left:651px;top:1174px;color:#4a5572">Low Voltage Wiring and Cabling<br>Voice and Data Network Cabling<br>CAT 3/5/6, Fiber Optic, and Coax Cabling<br>Single and Multiple Floor Installations</p>
<div class="btn-small" style="left:651px;top:1286px;background:var(--navy);color:var(--white)">Learn More</div>

<!-- Networking row -->
<div class="row" style="top:1374px;height:287px;background:var(--navy)"></div>
<div class="photo" role="img" aria-label="Rows of illuminated server racks in blue light" style="left:600px;top:1374px;width:600px;height:287px;background:radial-gradient(ellipse at 45% 55%,#3d78c8 0%,#1a4596 45%,#0b2358 100%)"></div>
<h3 class="svc-title" style="left:145px;top:1416px;color:var(--white)">Networking Setup</h3>
<p class="svc-list" style="left:145px;top:1460px;color:var(--white)">Server Racks/Networking Setup<br>Audio/Video Cabling and Wiring<br>WiFi - Wireless Network Installation<br>Access Point Installation</p>
<div class="btn-small" style="left:145px;top:1573px;border:1px solid var(--white);color:var(--white)">Learn More</div>

<!-- Installation row -->
<div class="row" style="top:1661px;height:285px;background:var(--panel)"></div>
<div class="photo" role="img" aria-label="Hands mounting a security camera with a power drill" style="left:0;top:1661px;width:600px;height:285px;background:linear-gradient(120deg,#8a6a58 0%,#c9d4dc 45%,#7aa9d4 70%,#c98a32 100%)"></div>
<svg class="abs" style="left:560px;top:1911px" width="80" height="35" viewBox="0 0 80 35"><polygon points="0,35 40,0 80,35" fill="var(--panel)"/></svg>
<h3 class="svc-title" style="left:650px;top:1702px;color:var(--ink)">Installation</h3>
<p class="svc-list" style="left:651px;top:1747px;color:#4a5572">Voice &amp; Telephone Wiring<br>Demarc Extension<br>Security Camera Installation<br>Heat Mapping</p>
<div class="btn-small" style="left:651px;top:1859px;background:var(--navy);color:var(--white)">Learn More</div>

<!-- Markets -->
<h2 class="markets-title">Markets</h2>
<article class="card" style="left:145px">
  <div class="pic" role="img" aria-label="Technician fitting a ceiling security camera" style="background:linear-gradient(160deg,#7c7f86 0%,#cfd3da 55%,#c9a07e 100%)"></div>
  <h3>Residential</h3>
  <p>Lorem Ipsum is simply dummy text of the printing and typesetting industry. Lorem Ipsum has been the industry's standard dummy text ever since the 1500s</p>
  <div class="more">READ MORE</div>
</article>
<article class="card featured" style="left:454px">
  <div class="pic" role="img" aria-label="Interior of a multi-level shopping mall" style="background:linear-gradient(180deg,#6e6a66 0%,#8a6a52 50%,#3e3832 100%)"></div>
  <h3>Commercial</h3>
  <p>Lorem Ipsum is simply dummy text of the printing and typesetting industry. Lorem Ipsum has been the industry's standard dummy text ever since the 1500s</p>
  <div class="more">READ MORE</div>
</article>
<article class="card" style="left:763px">
  <div class="pic" role="img" aria-label="Domed government capitol building under a blue sky" style="background:linear-gradient(180deg,#3d6fb8 0%,#8aa9d6 45%,#d6d6d2 75%,#5b5f5c 100%)"></div>
  <h3>Federal</h3>
  <p>Lorem Ipsum is simply dummy text of the printing and typesetting industry. Lorem Ipsum has been the industry's standard dummy text ever since the 1500s</p>
  <div class="more">READ MORE</div>
</article>

<!-- Footer -->
<footer class="footer">
  <div class="foot-brand"><i></i>BRIGHTWIREL</div>
  <span class="social" style="left:157px"></span>
  <span class="social" style="left:190px"></span>
  <span class="social" style="left:222px"></span>
  <span class="social" style="left:255px"></span>

  <h4 class="foot-h" style="left:362px;top:31px">Contact Us</h4>
  <svg class="icon" style="top:78px" width="18" height="18" viewBox="0 0 24 24"><path fill="#fff" d="M6.6 10.8a15.1 15.1 0 0 0 6.6 6.6l2.2-2.2c.3-.3.7-.4 1-.2 1.1.4 2.3.6 3.6.6.6 0 1 .4 1 1V20c0 .6-.4 1-1 1A17 17 0 0 1 3 4c0-.6.4-1 1-1h3.5c.6 0 1 .4 1 1 0 1.3.2 2.5.6 3.6.1.3 0 .7-.2 1z"/></svg>
  <div class="contact" style="top:74px">Phone: +847-555-0172</div>
  <svg class="icon" style="top:115px" width="18" height="16" viewBox="0 0 24 20"><path fill="#fff" d="M2 0h20a2 2 0 0 1 2 2v.5L12 10 0 2.5V2a2 2 0 0 1 2-2zm-2 5 12 7.5L24 5v13a2 2 0 0 1-2 2H2a2 2 0 0 1-2-2z"/></svg>
  <div class="contact" style="top:110px">Email:&nbsp; Support@Brightwirel.com</div>
  <svg class="icon" style="top:158px" width="18" height="24" viewBox="0 0 18 24"><path fill="#fff" d="M9 0a9 9 0 0 0-9 9c0 6.8 9 15 9 15s9-8.2 9-15a9 9 0 0 0-9-9zm0 12.5A3.5 3.5 0 1 1 9 5.5a3.5 3.5 0 0 1 0 7z"/></svg>
  <div class="contact" style="top:151px">418 Harbor Crest Ct.<br>Maple Ridge, TX 77501</div>

  <div class="divider-v"></div>
  <h4 class="foot-h" style="left:793px;top:33px">Services</h4>
  <span class="foot-link" style="left:793px;top:64px">Home</span>
  <span class="foot-link" style="left:793px;top:94px">Low Voltage</span>
  <span class="foot-link" style="left:793px;top:123px">Markets</span>
  <span class="foot-link" style="left:793px;top:153px">Our Team</span>
  <span class="foot-link" style="left:793px;top:182px">Contact Us</span>
  <span class="foot-link" style="left:932px;top:64px">Wiring and Cabling</span>
  <span class="foot-link" style="left:932px;top:97px">Networking Setup</span>
  <span class="foot-link" style="left:932px;top:130px">Camera Installation</span>
  <span class="foot-link" style="left:932px;top:165px">Services</span>

  <div class="divider-h"></div>
  <p class="copy">Brightwirel © 2021 All Rights Reserved | Privacy Policy | Terms and Conditions</p>
</footer>

</body>
</html>
```